Brel Fosk Painting, Eco and Non toxic painting client information brochure.

Brel fosk painting is a painting company that specialises in eco and non toxic paints. This brochure will be left with the client after the initial meeting to explain about my business and hopefully win the job. By reading the text i have provided (see attachment) you can get a better understanding of what we do.
The brochure should be fresh and clean looking, complimenting the Brel Fosk Painting logo and the text provided.
This will be printed onto a recycled paper.
Text and font must clear and easy to read.

Please have a look at my web page. I will be redoing this soon as well but this will give you some ideas of where I'm at.

Would like some picture but not sure what.
I have attached some pics but they don't have to be use
Updates

Hi peeps,

Thanks for all the great designs and sorry i haven't got back to you sooner.
been a bit busy.
Tomorrow i hope to be able to sit down and have a good look at what everybody has done.
Thanks again i really appreciate the effort.

kind regards oswin 

hi designers,

Just sat down and had a good look at the designs sent in and there are some crackers.
Its going to be very difficult to choose. I have only 1 day left before it closes so ill wait till then to see if there are any more submissions come in then ill get back to everybody.
Thanks again for your time and effort.

kind regards oswin 

Hi too all you designers that have worked on my project. 

I am always amazed at all the different designs that come through. Super work guys and girls. 
I have narrowed it down to a couple of designs.
Ill be making the decision tonight.
Thanks again to you all and i really appreciate all the hard work.
I will be doing another brochure in the future for more architecture / builder focus and there were a few designs that would work perfectly for this.

Kinds regards oswin  

Target Market(s)

The work we do is mainly residential repaints, family homes
Mostly I am dealing with the wife of the family or female designers/architects

Industry/Entity Type

Painting

Requirements
Must have
• Company logo, either white or black version what ever suits best.
Text that has been provided.
Brochure will be 1 page A 4, folded into 3 parts both sides.
Front page must have logo and
SPECIALSING IN:
NON TOXIC
ECO FRIENDLY &
HEAT REFLECTIVE PAINTS
Phone 041 382 6190
Painting@brelfosk.biz
www.brelfosk.biz

```html
<!DOCTYPE html>
<html lang="en">
<head>
<meta charset="utf-8">
<title>Brel Fosk Painting – Client Brochure, Inside Spread</title>
<link rel="stylesheet" href="https://fonts.googleapis.com/css2?family=Cabin:wght@400;500;700&family=Cabin+Condensed:wght@600;700&display=swap">
<style>
  :root {
    --stage: #ebe6da;
    --paper: #ffffff;
    --ink: #2f2f2f;
    --green-deep: #3b8f2c;
    --green-mid: #5aab33;
    --green-bright: #8cc63f;
    --green-wash: #c4df72;
    --frame: #c9e69c;
    --heading-green: #2f7d26;
    --room-grey: #c9cccc;
    --room-orange: #e0782e;
    --room-yellow: #f2cf2a;
    --room-lime: #b8d43a;
    --floor: #eef0ea;
  }
  * { box-sizing: border-box; margin: 0; padding: 0; }
  html, body {
    width: 1200px; height: 913px; overflow: hidden;
    background: var(--stage);
    font-family: "Cabin", Arial, sans-serif;
  }
  .brochure {
    position: absolute; left: 60px; top: 66px;
    width: 1080px; height: 780px;
    display: flex;
    box-shadow: 0 10px 30px rgba(0,0,0,.18);
  }
  .panel { position: relative; width: 360px; height: 100%; overflow: hidden; }

  .section-head {
    position: absolute; height: 26px; display: flex; align-items: center;
    font-family: "Cabin Condensed", Arial, sans-serif;
    font-weight: 700; font-size: 15px; letter-spacing: .4px; text-transform: uppercase;
    z-index: 2;
  }
  .section-head .bar { height: 26px; }
  .body-copy { font-size: 12.5px; line-height: 1.78; color: var(--ink); }
  .body-copy p + p { margin-top: 8px; }

  /* Left panel */
  .panel--about { background: linear-gradient(180deg, var(--paper) 0%, var(--paper) 58%, #eef6d6 72%, var(--green-wash) 100%); }
  .panel--about .section-head { left: 0; color: var(--heading-green); }
  .panel--about .section-head .bar { width: 130px; background: linear-gradient(90deg, var(--green-deep), var(--green-mid)); margin-right: 22px; }
  .head-company { top: 36px; }
  .head-owner { top: 596px; }
  .copy-company { position: absolute; top: 78px; left: 30px; right: 44px; }
  .copy-owner { position: absolute; top: 638px; left: 30px; right: 44px; }

  /* Middle panel */
  .panel--green { background: linear-gradient(90deg, var(--green-mid) 0%, var(--green-deep) 30%, var(--green-mid) 75%, #7cbc45 100%); }
  .panel--green .section-head { top: 30px; left: 0; color: #fff; }
  .panel--green .section-head .bar { width: 130px; background: var(--green-bright); margin-right: 28px; }
  .copy-green { position: absolute; top: 74px; left: 32px; right: 40px; color: #fff; }
  .room-yellow {
    position: absolute; left: 0; top: 430px; width: 360px; height: 350px;
    background:
      linear-gradient(180deg, transparent 0%, transparent 80%, rgba(255,248,225,.85) 88%, var(--floor) 100%),
      radial-gradient(ellipse 55% 45% at 58% 30%, #fff2a8 0%, #f8de4a 40%, transparent 75%),
      linear-gradient(180deg, var(--room-yellow) 0%, #eebd22 70%, #e3a91c 100%);
  }
  .curve-left { position: absolute; left: 0; top: 430px; width: 360px; height: 350px; }
  .photo-frame {
    position: absolute; left: 18px; top: 232px; width: 324px; height: 250px;
    border-radius: 34px; background: var(--frame); padding: 14px;
    box-shadow: 0 4px 12px rgba(0,0,0,.18);
    z-index: 2;
  }
  .room-grey {
    width: 100%; height: 100%; border-radius: 22px;
    background:
      linear-gradient(180deg, transparent 0%, transparent 62%, rgba(90,90,85,.45) 78%, rgba(110,105,95,.7) 100%),
      radial-gradient(ellipse 30% 30% at 10% 40%, #f4f7ef 0%, transparent 70%),
      linear-gradient(180deg, #f2f3f2 0%, var(--room-grey) 60%, #a6a6a0 100%);
  }

  /* Right panel */
  .panel--hire { background: var(--paper); }
  .panel--hire .section-head { top: 40px; right: 0; color: var(--heading-green); }
  .panel--hire .section-head .bar { width: 110px; background: linear-gradient(90deg, var(--green-mid), var(--green-bright)); margin-left: 14px; }
  .copy-hire { position: absolute; top: 84px; left: 26px; right: 40px; }
  .room-orange {
    position: absolute; left: 0; top: 180px; width: 360px; height: 282px;
    background:
      linear-gradient(180deg, transparent 0%, transparent 80%, #d6b24c 86%, #c69a3c 94%, #e8e4da 100%),
      radial-gradient(ellipse 40% 35% at 55% 45%, #f0944a 0%, transparent 75%),
      linear-gradient(180deg, #e9873a 0%, var(--room-orange) 70%, #d86e28 100%);
  }
  .wave-right { position: absolute; left: 0; top: 168px; width: 360px; height: 112px; z-index: 1; }
  .room-lime {
    position: absolute; left: 30px; top: 462px; width: 330px; height: 318px;
    background:
      linear-gradient(180deg, transparent 0%, transparent 70%, rgba(240,244,232,.9) 78%, var(--floor) 100%),
      radial-gradient(ellipse 50% 40% at 50% 35%, #d9e86e 0%, transparent 75%),
      linear-gradient(180deg, #c6dc4a 0%, var(--room-lime) 70%, #a9c534 100%);
  }
  .room-yellow-edge {
    position: absolute; left: 0; top: 462px; width: 30px; height: 318px;
    background: linear-gradient(180deg, #f0c828 0%, #e8b322 72%, var(--floor) 88%);
  }
  .fold { position: absolute; top: 0; width: 1px; height: 100%; background: rgba(0,0,0,.08); z-index: 3; }
</style>
</head>
<body>
  <main class="brochure">
    <section class="panel panel--about">
      <h2 class="section-head head-company"><span class="bar"></span>About the Company</h2>
      <div class="body-copy copy-company">
        <p>At Brel Fosk Painting we provide a high-quality service and exceptional craftsmanship for both domestic and commercial projects. We are proud to say we are making our work practices and business support processes more sustainable. We want to be sure we are doing our part to reduce our carbon footprint.</p>
        <p>We take the time to research alternative eco painting products and processes. We can also provide you with information about the products and why we use them. All our jobs are professionally finished utilising only the best tools and products available.</p>
        <p>We aim to limit the interruption to clients and their families as a result of our work; safety is paramount. We make sure that you are satisfied with the work done and will communicate with you throughout the job.</p>
        <p>Brel Fosk Painting is dedicated to learning, understanding and implementing new products and techniques that will be safer for the environment and your family. All this is done at a competitive price</p>
      </div>
      <h2 class="section-head head-owner"><span class="bar"></span>About the Owner</h2>
      <div class="body-copy copy-owner">
        <p>Brel Fosk has been painting for over 20 years. He is an accredited Green Painter and is often called upon by architects and builders to provide advice on sustainable products and methods.</p>
      </div>
    </section>

    <section class="panel panel--green">
      <h2 class="section-head"><span class="bar"></span>Going Green</h2>
      <div class="body-copy copy-green">
        <p>We can help you make smart decisions about creating a better environment and further minimizing any risk for your family and the spaces we live in. This can be achieved reducing the amount of VOCs (volatile organic compounds) by selecting the correct products.</p>
      </div>
      <div class="room-yellow" role="img" aria-label="Photo of a yellow-walled room with a pendant lamp, low bench, bonsai and orange chair"></div>
      <svg class="curve-left" viewBox="0 0 360 350" aria-hidden="true">
        <path d="M0 0 H140 C60 60 40 200 120 350 H0 Z" fill="#3b8f2c"/>
        <path d="M140 0 C60 60 40 200 120 350 H104 C24 200 44 60 124 0 Z" fill="#8cc63f"/>
      </svg>
      <div class="photo-frame">
        <div class="room-grey" role="img" aria-label="Photo of a modern grey living room with sofa, coffee table, shelving and a bright window"></div>
      </div>
    </section>

    <section class="panel panel--hire">
      <h2 class="section-head">Hiring a Professional<span class="bar"></span></h2>
      <div class="body-copy copy-hire">
        <p>Hiring a professional painter is never an easy decision and should not be taken lightly. Painting is a highly skilled trade and it takes considerable experience and expertise to obtain a high quality finish.</p>
      </div>
      <div class="room-orange" role="img" aria-label="Photo of an orange-walled lounge with a white sofa, framed flower print, potted plant and shaggy rug"></div>
      <svg class="wave-right" viewBox="0 0 360 112" preserveAspectRatio="none" aria-hidden="true">
        <path d="M0 0 H360 V62 C220 52 100 62 0 96 Z" fill="#ffffff"/>
        <path d="M0 96 C100 62 220 52 360 62 V76 C220 66 100 76 0 112 Z" fill="#8cc63f"/>
      </svg>
      <div class="room-yellow-edge" aria-hidden="true"></div>
      <div class="room-lime" role="img" aria-label="Photo of a lime green room with a white sofa, green cushions and zigzag wall shelf with vases"></div>
    </section>

    <span class="fold" style="left:360px"></span>
    <span class="fold" style="left:720px"></span>
  </main>
</body>
</html>
```